Web Design for Harbor Link Guild

We need a web design for Harbor Link Guild. You can see more details about the kind of business that it deals with in this link: http://harborlinkguild.example/. The concept of the site is similar to http://www.volmari.example/ and we are looking for a homepage design also similar to it.
The top navigation should have:
1) directory
2) articles
3) deals
4) forums
5) log in/register page.
It should also have a video, a slider, map & text as well as a call to action to a "why register page".
As part of the footer it should include:
1) about HLG
2) contact HGL
3) terms & conditions
4) privacy
The color palette for the site will be the UAE flag colors which are red, green, white and black.
Updates
Project Deadline Extended
Reason: We need more designs and options.
Keep sending in more creative designs. thanks.
Industry/Entity Type
Business
Look and feel
Each slider illustrates characteristics of the customer's brand and the style your logo design should communicate.

```html
<!DOCTYPE html>
<html lang="en">
<head>
<meta charset="utf-8">
<title>Harbor Link Guild</title>
<link rel="stylesheet" href="https://fonts.googleapis.com/css2?family=Roboto:wght@300;400;500;700&family=Roboto+Condensed:wght@700&display=swap">
<style>
:root{
  --green:#1a9b46;
  --green-dark:#0f7a2e;
  --red:#e8322a;
  --black:#111;
  --ink:#333;
  --grey-bar:#dcdcdc;
  --hero:#dedede;
  --line:#cfcfcf;
  --white:#fff;
  --footer:#2b2b2b;
  --sky:#8ab8dc;
}
*{box-sizing:border-box;margin:0;padding:0}
a{text-decoration:none}
html,body{width:1200px;height:1198px;overflow:hidden}
body{font-family:'Roboto',sans-serif;color:var(--ink);background:var(--white);position:relative}
.abs{position:absolute}
.topbar{left:0;top:0;width:1200px;height:44px;background:var(--grey-bar)}
.contact-line{right:47px;top:14px;font-size:16px;font-weight:300;color:var(--black);display:flex;align-items:center;gap:8px}
.contact-line .t{color:var(--green)}
.contact-line .f{color:var(--red)}
.login{background:var(--black);color:var(--white);font-size:13px;font-weight:500;padding:4px 6px;margin-left:4px}
.navband{left:0;top:47px;width:1200px;height:98px;background:var(--white);box-shadow:0 1px 3px rgba(0,0,0,.15)}
.hero{left:0;top:145px;width:1200px;height:461px;background:radial-gradient(ellipse at 40% 40%,#ececec,#d4d4d4)}
.logo-disc{left:47px;top:-4px;width:196px;height:196px;border-radius:50%;background:var(--white);box-shadow:0 2px 4px rgba(0,0,0,.15)}
.logo-name{left:168px;top:80px;font-size:30px;font-weight:500;color:var(--green);letter-spacing:-.5px}
.nav{left:564px;top:47px;display:flex;height:78px}
.nav a{color:var(--ink);font-size:14px;display:flex;align-items:center;padding:0 29px}
.nav a.home{background:var(--green);color:var(--white);font-weight:500;padding:0 14px;width:68px;justify-content:center;margin-right:12px}
.emblem{left:47px;top:226px;width:64px;height:84px;background:linear-gradient(#f0c030,#c89a20);border-radius:8px 8px 30px 30px}
.project{left:122px;top:236px;width:330px;text-align:center;font-family:'Roboto Condensed',sans-serif;font-weight:700;font-size:19px;line-height:22px;color:var(--black)}
.project .who{color:#b8901a}
.intro{left:56px;top:326px;width:410px;font-size:20px;font-weight:300;line-height:34px;color:#222}
.register{left:107px;top:480px;width:274px;height:66px;border-radius:33px;background:var(--white);padding:3px;box-shadow:0 2px 4px rgba(0,0,0,.25)}
.register span{display:flex;align-items:center;justify-content:center;height:100%;border-radius:30px;background:linear-gradient(#2eab3e,#0d6a1f);color:var(--white);font-family:'Roboto Condensed',sans-serif;font-weight:700;font-size:28px}
.video{left:497px;top:172px;width:656px;height:417px;background:var(--white);padding:10px}
.video-inner{width:100%;height:100%;background:var(--black);padding:5px 6px;position:relative}
.screen{width:100%;height:354px;background:radial-gradient(circle at 50% 45%,#a8cce8,var(--sky))}
.play{left:50%;top:147px;width:98px;height:98px;margin-left:-49px;border-radius:50%;background:var(--black);border:3px solid #444}
.controls{left:6px;bottom:6px;right:6px;height:30px;display:flex;align-items:center;gap:4px;color:var(--white);font-size:11px}
.btn{width:27px;height:26px;background:#eee;display:flex;align-items:center;justify-content:center}
.track{flex:1;height:4px;background:var(--white);margin:0 6px;position:relative}
.track i{position:absolute;left:0;top:0;width:34%;height:4px;background:#2a7fd0}
.hd{border:2px solid #f0c020;border-radius:3px;padding:0 3px;font-weight:700;margin-left:6px}
.partners{left:0;top:606px;width:1200px;height:83px;background:#f4f4f4;border:1px solid var(--line);display:flex;align-items:center;justify-content:space-around;padding:0 30px}
.partners span{font-size:15px;font-weight:500;color:#444;letter-spacing:1px;display:flex;align-items:center;gap:6px}
.partners span b{display:inline-block;width:14px;height:14px;background:#777}
.divider-v{left:779px;top:689px;width:1px;height:400px;background:var(--line)}
.welcome{left:50px;top:707px;width:715px}
.welcome h1{font-size:23px;font-weight:500;color:var(--red);margin-bottom:2px}
.welcome p{font-size:14px;line-height:18px;color:#333;margin-bottom:6px}
.divider-h{left:47px;top:903px;width:732px;height:1px;background:var(--line)}
.clients{left:50px;top:920px;width:700px}
.clients h2{font-size:17px;font-weight:400;color:#333;display:flex;align-items:center;gap:6px}
.clients h2 b{display:inline-block;width:16px;height:16px;border-radius:50%;background:#666}
.clients blockquote{margin-top:16px;font-size:14px;line-height:18px;color:#333}
.clients blockquote::before{content:"\201C";color:#bbb;font-size:30px;line-height:0;vertical-align:-10px;margin-right:6px}
.clients blockquote::after{content:"\201D";color:#bbb;font-size:30px;line-height:0;vertical-align:-14px}
.who-said{left:48px;top:1038px;font-size:15px;color:#222}
.who-said small{display:block;font-size:13px;color:#444}
.see-all{left:641px;top:1037px;width:99px;height:30px;border:1px solid #ccc;background:linear-gradient(#fff,#ececec);font-size:13px;font-weight:500;display:flex;align-items:center;justify-content:center;color:#111}
.infographic{left:795px;top:718px;width:360px;height:340px;border-radius:50%;background:radial-gradient(circle at 50% 30%,#e8a09a,#d9d9d9 55%,#b8d8bd)}
.footer{left:0;top:1089px;width:1200px;height:109px;background:var(--footer);border-top:3px solid var(--green);color:var(--white)}
.copy{left:48px;top:30px;width:650px;font-size:14px}
.copy p{font-size:11px;line-height:13px;margin-top:2px}
.social{right:44px;top:14px;display:flex;gap:8px}
.social i{width:32px;height:32px;border-radius:3px;background:#2a6bb0;display:block}
.footlinks{right:47px;top:63px;font-size:14px}
</style>
</head>
<body>
<div class="abs topbar"></div>
<div class="abs contact-line"><span><span class="t">T:</span> +971 (4) 555 0142</span>|<span><span class="f">F:</span> +971 (4) 555 0178</span><span class="login">MEMBER LOGIN HERE</span></div>
<div class="abs navband"></div>
<div class="abs hero"></div>
<div class="abs logo-disc"></div>
<div class="abs logo-name">Harbor Link Guild</div>
<nav class="abs nav">
  <a class="home" href="#">Home</a><a href="#">Directory</a><a href="#">Articles</a><a href="#">Deals</a><a href="#">Forums</a><a href="#" style="padding-right:0">Contact Us</a>
</nav>

<div class="abs emblem" role="img" aria-label="National emblem"></div>
<div class="abs project">A<br><span class="who">Sheikh Karim bin Faris Al Nadeem</span><br>Project</div>
<p class="abs intro">An online business networking plateform exclusive for UAE Freezone Companies, where they can learn, communicate effectively and benefit from working with each other.</p>
<a class="abs register" href="#"><span>REGISTER NOW</span></a>

<div class="abs video">
  <div class="video-inner">
    <div class="screen" role="img" aria-label="Introductory video preview"></div>
    <div class="abs play"><svg width="92" height="92" viewBox="0 0 92 92"><polygon points="36,26 68,46 36,66" fill="#fff"/></svg></div>
    <div class="abs controls">
      <span class="btn"><svg width="12" height="12"><polygon points="1,0 12,6 1,12" fill="#000"/></svg></span>
      <span class="btn"><svg width="12" height="12"><rect x="1" width="3" height="12" fill="#000"/><rect x="8" width="3" height="12" fill="#000"/></svg></span>
      <span class="btn"><svg width="12" height="12"><rect width="12" height="12" fill="#000"/></svg></span>
      <span class="track"><i></i></span>
      <span>00:58 / 3:02</span><span class="hd">HD</span>
      <svg width="70" height="20"><circle cx="8" cy="8" r="5" fill="#eee"/><circle cx="14" cy="14" r="5" fill="#eee"/><circle cx="40" cy="10" r="7" fill="none" stroke="#e33" stroke-width="2"/><polygon points="50,18 68,4 68,18" fill="#eee"/></svg>
    </div>
  </div>
</div>

<div class="abs partners">
  <span><b></b>Vantor Interactive</span><span>ELOKA</span><span>SPAN MEDIA</span><span>Dalby-Wren</span><span>ORBIX</span><span>TRADIVO</span><span>FRESH FIELD</span><span><b></b>QRT Marketing</span>
</div>

<div class="abs divider-v"></div>
<section class="abs welcome">
  <h1>Welcome to Our Website:</h1>
  <p>Lorem Ipsum is simply dummy text of the printing and typesetting industry. Lorem Ipsum has been the industry's standard dummy text ever since the 1500s, when an unknown printer took a galley of type and scrambled it to make a type specimen book. It has survived not only five centuries, but also the leap into electronic typesetting, remaining essentially unchanged.</p>
  <p>It was popularised in the 1960s with the release of Letraset sheets containing Lorem Ipsum passages, and more recently with desktop publishing software like Aldus PageMaker including versions of Lorem Ipsum. It was popularised in the 1960s with the release of Letraset sheets containing Lorem Ipsum passages, and more recently with desktop publishing software like Aldus PageMaker including versions of Lorem Ipsum.</p>
</section>
<div class="abs divider-h"></div>
<section class="abs clients">
  <h2><b></b>What Our Clients Says:</h2>
  <blockquote>Lorem Ipsum is simply dummy text of the printing and typesetting industry. It has survived not only five centuries, but also the leap into electronic typesetting including versions of Lorem Ipsum. Lorem Ipsum is simply dummy text of the printing and typesetting industry. It has survived not only five centuries, but also the leap into electronic typesetting including versions of Lorem Ipsum.</blockquote>
</section>
<div class="abs who-said">Happy Client<small>Designation</small></div>
<a class="abs see-all" href="#">» See All</a>

<div class="abs infographic" role="img" aria-label="Three-step infographic illustration in red, black and green"></div>

<footer class="abs footer">
  <div class="abs copy">© 2013, Harbor Link Guild | All Rights Reserved.
    <p>Lorem Ipsum is simply dummy text of the printing and typesetting industry. Lorem Ipsum has been the industry's standard dummy text ever since the 1500s, when an unknown printer took a galley of type and scrambled it to make a type specimen book.</p>
  </div>
  <div class="abs social" role="img" aria-label="Social media links"><i></i><i></i><i></i></div>
  <div class="abs footlinks">Home | About HLG | Contact HGL | Terms &amp; Conditions | Privacy</div>
</footer>
</body>
</html>
```